KVR Inc Web Design

WHAT ARE WE DOING?
We are developing a new website look and feel for a new company called KVR Inc. This new look and feel should include colors, design elements, choice of photography and other imagery, fonts, and other user experience elements.

WHAT DO THEY DO?
KVR, Inc, makes tools for researchers who are studying protein-protein interactions. These molecules are the basic tools of biology, and serve as key targets for drug developers and disease researchers. The world of proteins is enormously complex, and companies like KVR provide researchers with critical tools that help them elucidate this world.

WHO ARE WE TALKING TO?
The target audience for this website are professional scientists working in university research or biopharma drug development. They are highly sophisticated consumers looking for key tools that will advance their research.

WHAT DO WE WANT THEM TO DO?
The site is an information resource for the customer exploring the tools that KVR sells and the scientific issues surrounding protein-protein interactions. They should be able to navigate easily to their content of choice, while the whole site should convey a professionalism that enhanced KVR’s credibility.

WHAT DOES THE KVR BRAND STAND FOR?
KVR stands for illumination. Proteins are challenging to study, and KVR exists to help shed light on their workings.

WHAT ARE THE KEY VALUES OF THE KVR BRAND?
Integrity. Innovation. Insight.

WHAT ARE THE EXECUTIONAL MANDITORIES?
The look and feel is completely up for grabs. Nothing is off the table.

WHAT ARE THE DELIVERABLES?
We need new designs for the following templates:
http://cms.marlowbench.com/
http://cms.marlowbench.com/products-and-services/instruments-3/bench-top-instruments/
http://cms.marlowbench.com/category/lab-study/

```html
<!DOCTYPE html>
<html lang="en">
<head>
<meta charset="utf-8">
<title>KVR Inc — Pipettes</title>
<link href="https://fonts.googleapis.com/css2?family=Figtree:wght@400;500;600;700&family=Source+Sans+3:wght@400;600&display=swap" rel="stylesheet">
<style>
  :root {
    --orange: #fdb84a;
    --orange-text: #f7a72a;
    --brown: #5b4633;
    --cyan: #30b4d6;
    --panel: #f3f1f1;
    --ink: #111111;
    --body: #555555;
    --tab: #e4e2e2;
    --rule: #d6d6d6;
    --white: #ffffff;
  }
  * { box-sizing: border-box; margin: 0; padding: 0; }
  html, body { width: 1200px; height: 1143px; overflow: hidden; background: var(--white); }
  body { font-family: "Figtree", sans-serif; color: var(--body); position: relative; }
  a { color: inherit; text-decoration: none; }

  .site-header { position: absolute; left: 0; top: 0; width: 1200px; height: 62px; background: var(--orange); }
  .brand { position: absolute; left: 190px; top: 16px; font-size: 23px; font-weight: 400; letter-spacing: 4px; color: var(--white); line-height: 30px; white-space: nowrap; }
  .main-nav { position: absolute; left: 340px; top: 16px; display: flex; align-items: center; height: 26px; }
  .main-nav a { color: var(--white); font-size: 13.2px; font-weight: 600; padding: 0 9px; line-height: 26px; border-radius: 13px; white-space: nowrap; }
  .main-nav a.active { background: var(--brown); padding: 0 10px; margin: 0 1px; }
  .search { position: absolute; left: 892px; top: 18px; width: 118px; height: 21px; background: rgba(120,90,40,0.28); border-radius: 2px; }
  .search span { position: absolute; left: 7px; top: 3px; font-size: 11px; color: #f4e6cc; }
  .search svg { position: absolute; right: 5px; top: 4px; }

  .sidebar { position: absolute; left: 190px; top: 99px; width: 216px; }
  .side-title { height: 39px; background: var(--cyan); color: var(--white); font-size: 18px; font-weight: 700; padding: 8px 0 0 23px; }
  .side-list { background: var(--panel); height: 125px; padding-top: 10px; list-style: none; }
  .side-list li { height: 28.5px; line-height: 28.5px; padding-left: 25px; font-size: 13px; color: var(--ink); font-weight: 500; }
  .side-list li.current { background: var(--orange); color: var(--white); }
  .news { background: var(--cyan); height: 135px; padding: 22px 20px 0 19px; color: var(--white); }
  .news h2 { font-size: 18px; font-weight: 700; margin-bottom: 7px; }
  .news p { font-size: 11.2px; line-height: 14.5px; padding-left: 1px; }

  .content { position: absolute; left: 433px; top: 99px; width: 577px; }
  .page-title { font-size: 23px; font-weight: 500; color: var(--ink); letter-spacing: 0.5px; height: 37px; padding-top: 4px; border-bottom: 1px solid #bbbbbb; }
  .page-title + .rule { height: 3px; border-bottom: 1px solid #cccccc; }
  .hero { margin-top: 4px; height: 240px; background: linear-gradient(100deg, #d9dde0 0%, #eef0f1 40%, #f6f4f2 70%, #e6e2de 100%); }
  .lead { margin-top: 18px; font-size: 18.5px; line-height: 23.5px; color: var(--ink); font-weight: 400; }
  .body-text { margin-top: 8px; font-size: 11.5px; line-height: 16px; color: var(--body); }
  .body-text p + p { margin-top: 16px; }
  .hl { color: var(--orange-text); font-weight: 600; }

  .tabs { position: absolute; left: 434px; top: 718px; display: flex; height: 31px; }
  .tabs div { height: 31px; line-height: 31px; text-align: center; font-family: "Source Sans 3", sans-serif; font-size: 14px; color: #555555; background: var(--tab); border-right: 1px solid var(--white); position: relative; }
  .tabs div.active { background: var(--orange); color: var(--white); }
  .tabs div.active::after { content: ""; position: absolute; left: 50%; bottom: -6px; margin-left: -6px; border: 6px solid transparent; border-bottom: 0; border-top-color: var(--orange); }

  .tab-photo { position: absolute; left: 436px; top: 766px; width: 217px; height: 217px; background: linear-gradient(135deg, #2d5a98 0%, #5f8ac4 45%, #c6b9a8 75%, #8aa7c9 100%); }
  .tab-text { position: absolute; left: 664px; top: 764px; width: 344px; font-size: 11.3px; line-height: 16px; }
  .tab-text p + p { margin-top: 16px; }

  .site-footer { position: absolute; left: 190px; top: 1018px; width: 820px; border-top: 1px solid var(--rule); text-align: center; }
  .footer-mark { width: 23px; height: 3px; background: var(--orange); margin: 23px auto 0; }
  .footer-nav { margin-top: 14px; font-size: 11px; color: #444444; }
  .footer-nav span { margin: 0 5px; }
  .copyright { margin-top: 5px; font-size: 11.5px; color: #555555; }
  .social { margin-top: 6px; display: flex; justify-content: center; gap: 4px; }
  .social i { width: 16px; height: 16px; border-radius: 50%; background: #5a5a5a; display: block; }
</style>
</head>
<body>
  <header class="site-header">
    <div class="brand">KVR INC</div>
    <nav class="main-nav">
      <a href="#">Company</a>
      <a href="#" class="active">Products &amp; Services</a>
      <a href="#">Learning Center</a>
      <a href="#">Events</a>
      <a href="#">KVR News</a>
      <a href="#">Contact</a>
    </nav>
    <div class="search">
      <span>Search</span>
      <svg width="12" height="12" viewBox="0 0 12 12" aria-hidden="true"><circle cx="5" cy="5" r="3.6" fill="none" stroke="#e9d6b3" stroke-width="1.3"/><line x1="7.6" y1="7.6" x2="11" y2="11" stroke="#e9d6b3" stroke-width="1.5"/></svg>
    </div>
  </header>

  <aside class="sidebar">
    <div class="side-title">Product Overview</div>
    <ul class="side-list">
      <li>Reagents</li>
      <li class="current">Pipettes</li>
      <li>Tubes</li>
    </ul>
    <div class="news">
      <h2>Latest News</h2>
      <p>October 7, 2013 : Lorem ipsum dolor sit &nbsp;amet, consect eturelus mod &nbsp;adipisicing elit, sed do eiusmod tempor</p>
    </div>
  </aside>

  <main class="content">
    <h1 class="page-title">PIPETTES</h1>
    <div class="rule"></div>
    <div class="hero" role="img" aria-label="Three scientists in lab coats examining a flask of liquid beside coloured glassware"></div>
    <p class="lead">Donec non massa lacinia, commodo eros eget, rutrum arcu. Integer tincidunt, velit id eleifend congue, odio massa consequat mauris,</p>
    <div class="body-text">
      <p>Quisque feugiat lacus vitae posuere blandit. Nulla sit amet laoreet felis, id rhoncus nisl. Aenean fringilla quam in nibh egestas, in malesuada tortor accumsan. Donec non massa lacinia, commodo eros eget, rutrum arcu. Integer tincidunt, velit id eleifend congue, odio massa consequat mauris, a scelerisque nulla nulla eu nulla. Cras luctus pulvinar nibh ut viverra. Aenean vestibulum vitae justo non dictum. Mauris ut tellus in dui pretium dictum nec non tortor. Nulla a velit quis dolor interdum scelerisque eu et nisl.</p>
      <p>Donec auctor mollis ligula eget molestie. Aliquam erat volutpat. Curabitur sapien libero, condimentum ac nisl nec, ultricies tincidunt ipsum. Donec in iaculis metus. Mauris eleifend nisi non sapien commodo, hendrerit ornare lacus consectetur. Pellentesque faucibus, purus non dictum lacinia, ante augue pretium neque, vitae egestas dui nisl et enim. Suspendisse iaculis nibh vel lacinia rhoncus Donec auctor mollis ligula eget molestie. Aliquam erat volutpat. Curabitur sapien libero, condimentum ac nisl nec, ultricies tincidunt ipsum. Donec in iaculis metus. Mauris eleifend nisi non sapien commodo, hendrerit ornare lacus consectetur. Pellentesque faucibus, purus non dictum lacinia, ante augue pretium neque, <span class="hl">vitae egestas</span> dui nisl et enim. Suspendisse iaculis nibh vel lacinia rhoncus</p>
    </div>
  </main>

  <div class="tabs">
    <div class="active" style="width:120px">Overview</div>
    <div style="width:109px">Features</div>
    <div style="width:142px">Specifications</div>
    <div style="width:95px">FAQ's</div>
    <div style="width:110px;border-right:0">Manuals</div>
  </div>

  <div class="tab-photo" role="img" aria-label="Gloved researcher in protective gear using a pipette over a test tube"></div>
  <div class="tab-text">
    <p>Quisque feugiat lacus vitae posuere blandit. Nulla sit amet laoreet felis, id rhoncus nisl. Aenean fringilla quam in nibh egestas, in malesuada tortor accumsan. Donec non massa lacinia, commodo eros eget, rutrum arcu. Integer tincidunt, velit id eleifend congue, odio massa consequat mauris, a scelerisque nulla nulla eu nulla. Cras luctus pulvinar nibh ut viverra. Aenean vestibulum vitae justo non dictum. Mauris ut tellus in dui pretium dictum nec non tortor. Nulla a velit quis dolor interdum <span class="hl">scelerisque</span> eu et nisl.</p>
    <p>Donec auctor mollis ligula eget molestie. Aliquam erat volutpat. Curabitur sapien libero, condimentum ac nisl nec, ultricies tincidunt ipsum. Donec in iaculis metus. Mauris eleifend nisi non sapien commodo, hendrerit ornare lacus consectetur. Pellentesque faucibus, purus non dictum lacinia, ante augue</p>
  </div>

  <footer class="site-footer">
    <div class="footer-mark"></div>
    <nav class="footer-nav">Company<span>-</span>Products &amp; Services<span>-</span>Learning Center<span>-</span>Events<span>-</span>KVR News<span>-</span>Contact</nav>
    <p class="copyright">Copyright © KVR Inc. 2013</p>
    <div class="social"><i></i><i></i><i></i></div>
  </footer>
</body>
</html>
```